Kestrel Home Business Card Design

We need a business card for a Building company based in Queensland, Australia. Our colours are orange black and we do base all our homes design names and other aspect of our business on astrology. We want the consumer to perceive the company as professional and to attract investors to our company.We have over 20 years in the building industry.We pride ourselves on our innovation of designs and making the building process for anyone from families to investor a smooth and simple experience.
Business
Amelia Prichard0411752116PO Box 454, Mudgeerbaameliaprichard@zodiachomes.com

```html
<!DOCTYPE html>
<html lang="en">
<head>
<meta charset="utf-8">
<title>Kestrel Homes — Business Card</title>
<link rel="stylesheet" href="https://fonts.googleapis.com/css2?family=Open+Sans:wght@400;600;700&display=swap">
<style>
  :root {
    --orange: #f39320;
    --ink: #1a1a1a;
    --paper: #ffffff;
    --backdrop: #e9e6e1;
    --card-w: 900px;
    --card-h: 514px;
  }
  * { box-sizing: border-box; margin: 0; padding: 0; }
  html, body {
    width: 1200px; height: 1200px; overflow: hidden;
    background: var(--backdrop);
    font-family: "Open Sans", Arial, sans-serif;
    color: var(--ink);
  }
  .sheet {
    width: 1200px; height: 1200px;
    display: flex; flex-direction: column; align-items: center;
    justify-content: center; gap: 36px;
  }
  .card {
    position: relative;
    width: var(--card-w); height: var(--card-h);
    background: var(--paper);
    box-shadow: 0 6px 18px rgba(0,0,0,0.18);
    overflow: hidden;
  }

  /* Front */
  .card--front .brand {
    position: absolute; inset: 0 0 22px 0;
    display: flex; flex-direction: column; align-items: center; justify-content: center;
    gap: 34px; padding-bottom: 20px;
  }
  .brand__mark {
    width: 150px; height: 150px; border-radius: 50%;
    background: var(--orange);
  }
  .brand__name {
    font-weight: 700; font-size: 80px; letter-spacing: -1px;
    line-height: 1; color: var(--ink);
  }
  .card--front .edge-band {
    position: absolute; left: 0; right: 0; bottom: 0; height: 22px;
    background: var(--orange);
  }

  /* Back */
  .card--back { background: var(--orange); }
  .back__strip {
    position: absolute; left: 0; top: 0; bottom: 0; width: 230px;
    background: var(--paper);
    display: flex; flex-direction: column; align-items: center; justify-content: center;
    gap: 22px;
  }
  .back__mark {
    width: 150px; height: 150px; border-radius: 50%;
    background: var(--ink);
  }
  .back__brand {
    font-weight: 700; font-size: 24px; color: var(--ink); letter-spacing: -0.3px;
  }
  .contact {
    position: absolute; left: 290px; top: 168px;
  }
  .contact__name {
    font-weight: 600; font-size: 36px; letter-spacing: 1px; margin-bottom: 22px;
  }
  .contact__list { list-style: none; }
  .contact__item {
    display: flex; align-items: center; gap: 14px;
    font-size: 23px; letter-spacing: 0.8px; line-height: 1.45;
  }
  .contact__icon { width: 18px; height: 18px; flex: none; }
</style>
</head>
<body>
<main class="sheet">
  <section class="card card--front" aria-label="Card front">
    <div class="brand">
      <div class="brand__mark" aria-hidden="true"></div>
      <div class="brand__name">Kestrel Homes</div>
    </div>
    <div class="edge-band"></div>
  </section>

  <section class="card card--back" aria-label="Card back">
    <div class="back__strip">
      <div class="back__mark" aria-hidden="true"></div>
      <div class="back__brand">Kestrel Homes</div>
    </div>
    <div class="contact">
      <p class="contact__name">Harriet Colvane</p>
      <ul class="contact__list">
        <li class="contact__item">
          <svg class="contact__icon" viewBox="0 0 24 24" aria-hidden="true"><path d="M6.6 10.8a15.1 15.1 0 0 0 6.6 6.6l2.2-2.2a1 1 0 0 1 1-.25 11.4 11.4 0 0 0 3.6.57 1 1 0 0 1 1 1V20a1 1 0 0 1-1 1A17 17 0 0 1 3 4a1 1 0 0 1 1-1h3.5a1 1 0 0 1 1 1c0 1.25.2 2.45.57 3.57a1 1 0 0 1-.25 1z" fill="#fff"/></svg>
          <span>0487309625</span>
        </li>
        <li class="contact__item">
          <svg class="contact__icon" viewBox="0 0 24 24" aria-hidden="true"><path d="M12 2a7 7 0 0 0-7 7c0 5.2 7 13 7 13s7-7.8 7-13a7 7 0 0 0-7-7zm0 9.5A2.5 2.5 0 1 1 12 6.5a2.5 2.5 0 0 1 0 5z" fill="#fff"/></svg>
          <span>PO Box 872, Corrowah</span>
        </li>
        <li class="contact__item">
          <svg class="contact__icon" viewBox="0 0 24 24" aria-hidden="true"><rect x="2.5" y="5" width="19" height="14" rx="1" fill="none" stroke="#fff" stroke-width="2"/><path d="M3 6l9 7 9-7" fill="none" stroke="#fff" stroke-width="2"/></svg>
          <span>harrietcolvane@kestrelhomes.example</span>
        </li>
      </ul>
    </div>
  </section>
</main>
</body>
</html>
```